Mobile Fitness snd Therapy Business Card Design

I need a business card designed for my mobile fitness and therapy business.

Please view the images that I have uploaded. I like the simplicity of the design that I have attached. I adapted it with my information

Target Market(s)

Those seeking personal training, injury rehabilitation or massage therapy.

Industry/Entity Type

Business

Contact Information for Business Card

Derek Fulham - MSc, CAT(C), RMT, CSCS, Pn2
e-mail: derek@vantrelo.com
website: www.vantrelo.com
instagram: @derek_fulham

Font styles to use
Sans Serif

Colors
3176b5
0355a3

Requirements
Must have
• "Contact us to receive a FREE assessment"
• Services offered:
• Personal Training
• Golf Fitness
• Injury Rehab
• Massage Therapy
• Yoga
Nice to have
• Consistent colours with brand
• - Dark Blue: #232837
• - Blue: #5096f0
• Consistent look/feel with the website: www.vantrelo.com

```html
<!DOCTYPE html>
<html lang="en">
<head>
<meta charset="utf-8">
<title>Vantrelo Business Card</title>
<link rel="stylesheet" href="https://fonts.googleapis.com/css2?family=Open+Sans:wght@400;600;700&display=swap">
<style>
  :root {
    --navy: #232837;
    --blue: #5096f0;
    --blue-deep: #3176b5;
    --paper: #ffffff;
    --ink: #1d1f26;
    --backdrop: #e6e7ea;
  }
  * { box-sizing: border-box; margin: 0; padding: 0; }
  html, body { width: 1200px; height: 1200px; overflow: hidden; }
  body {
    background: var(--backdrop);
    font-family: "Open Sans", Arial, sans-serif;
    display: flex;
    flex-direction: column;
    align-items: center;
    justify-content: center;
    gap: 60px;
  }
  .card {
    width: 700px;
    height: 400px;
    position: relative;
    box-shadow: 0 6px 24px rgba(0,0,0,0.12);
    overflow: hidden;
  }

  /* Front */
  .card-front {
    background: var(--navy);
    color: var(--paper);
    display: flex;
    flex-direction: column;
    align-items: center;
    justify-content: center;
  }
  .brand-name {
    font-weight: 700;
    font-size: 72px;
    letter-spacing: 10px;
    line-height: 1;
    padding-left: 10px;
  }
  .brand-tagline {
    margin-top: 14px;
    font-weight: 600;
    font-size: 19px;
    letter-spacing: 5px;
    padding-left: 5px;
  }

  /* Back */
  .card-back { background: var(--paper); color: var(--ink); }
  .edge-tab {
    position: absolute;
    width: 16px;
    height: 150px;
    background: var(--navy);
  }
  .edge-tab.left { left: 0; top: 40px; border-radius: 0 14px 14px 0; }
  .edge-tab.right { right: 0; bottom: 40px; border-radius: 14px 0 0 14px; }

  .back-layout {
    position: absolute;
    left: 56px;
    top: 40px;
    right: 50px;
    display: flex;
  }
  .identity { width: 300px; padding-right: 26px; }
  .divider { width: 2px; background: var(--ink); margin-top: 70px; height: 170px; }
  .services { padding-left: 28px; padding-top: 4px; }

  .mini-brand { color: var(--navy); }
  .mini-brand .brand-name { font-size: 30px; letter-spacing: 4px; padding-left: 0; }
  .mini-brand .brand-tagline { font-size: 8px; letter-spacing: 2px; margin-top: 4px; padding-left: 0; }

  .person-name { margin-top: 38px; font-size: 30px; font-weight: 400; line-height: 1.1; }
  .credentials { font-size: 13px; color: var(--blue-deep); margin-top: 3px; }
  .contact-list { list-style: none; margin-top: 12px; }
  .contact-list li {
    display: flex; align-items: center; gap: 8px;
    font-size: 15px; line-height: 1.5;
  }
  .contact-list svg { width: 15px; height: 15px; flex: none; }

  .services-title { font-size: 18px; font-weight: 600; margin-bottom: 4px; }
  .services-list { list-style: none; }
  .services-list li { font-size: 15px; line-height: 1.55; }

  .cta {
    position: absolute;
    left: 0; right: 0; bottom: 30px;
    text-align: center;
    font-size: 20px;
    letter-spacing: 1.5px;
  }
</style>
</head>
<body>

<section class="card card-front">
  <div class="brand-name">VANTRELO</div>
  <div class="brand-tagline">NUTRITION - FITNESS - HEALTH</div>
</section>

<section class="card card-back">
  <div class="edge-tab left"></div>
  <div class="edge-tab right"></div>

  <div class="back-layout">
    <div class="identity">
      <div class="mini-brand">
        <div class="brand-name">VANTRELO</div>
        <div class="brand-tagline">NUTRITION - FITNESS - HEALTH</div>
      </div>
      <h1 class="person-name">Derek Fulham</h1>
      <p class="credentials">MSc, CAT(C), RMT, CSCS, Pn2</p>
      <ul class="contact-list">
        <li>
          <svg viewBox="0 0 16 16" aria-hidden="true"><path fill="#1d1f26" d="M3.5 1.5l2.5 0 1 3.5-1.7 1.2a8 8 0 0 0 4.5 4.5L11 9l3.5 1v2.5c0 1-.8 2-2 2C6.5 14.5 1.5 9.5 1.5 3.5c0-1.2 1-2 2-2z"/></svg>
          250-555-0143
        </li>
        <li>
          <svg viewBox="0 0 16 16" aria-hidden="true"><rect x="1" y="3" width="14" height="10" fill="#1d1f26"/><path d="M1.5 3.5L8 9l6.5-5.5" stroke="#fff" stroke-width="1.3" fill="none"/></svg>
          derek@vantrelo.com
        </li>
        <li>
          <svg viewBox="0 0 16 16" aria-hidden="true"><circle cx="8" cy="8" r="6.5" fill="none" stroke="#1d1f26" stroke-width="1.5"/><ellipse cx="8" cy="8" rx="2.8" ry="6.5" fill="none" stroke="#1d1f26" stroke-width="1.2"/><path d="M1.5 8h13" stroke="#1d1f26" stroke-width="1.2"/></svg>
          www.vantrelo.com
        </li>
        <li>
          <svg viewBox="0 0 16 16" aria-hidden="true"><rect x="1.5" y="1.5" width="13" height="13" fill="#1d1f26"/></svg>
          @derek_fulham
        </li>
      </ul>
    </div>

    <div class="divider"></div>

    <div class="services">
      <h2 class="services-title">Services offered:</h2>
      <ul class="services-list">
        <li>- Personal Training</li>
        <li>- Golf Fitness</li>
        <li>- Injury Rehab</li>
        <li>- Massage Therapy</li>
        <li>- Yoga</li>
        <li>- Group Training</li>
        <li>- Nutrition Coaching</li>
      </ul>
    </div>
  </div>

  <p class="cta">“Contact us to receive a FREE assessment”</p>
</section>

</body>
</html>
```